Marlow Dermal Studio - Business Banner with Brand Elements

Design:
• We would like to get a creative design for a wide banner that will go outside our medical spa clinic location. We need a designer to make a simple yet colorful and high-quality design layout. We want this banner to be eye-catching and to communicate the services we offer at our business: Laser Hair Removal | Veluxin | Lip Filler.

Requirements:
• We would like the banner to include our companies information which is the following:

Logo
“Refresh Your Skin”
Laser Hair Removal | Veluxin | Lip Filler
(520) 867-2291
www.MarlowDermalStudio.com

Colors:
• Our business colors are orange, a hint of black and white, but mostly peach/orange tones. (Orange: #f78f20 , White: #ffffff)

Fonts:
• Josefins Sans Bold & Lato

Content and images can be located here:
https://files.quibbleshare.com/share/folders/7tKwP3zRa9_LmQxVb2nD5yHc04EeJuFs8?mode=viewing

The following will give you an idea of our brand presentation:
• Our website is: www.MarlowDermalStudio.com
• Our Pictavo; @marlowdermalstudio
• Our Lumora: www.lumoranet.com/marlowdermalstudio

Target Market(s)
• Women 25 - 45

Industry/Entity Type
• Beauty

```html
<!DOCTYPE html>
<html lang="en">
<head>
<meta charset="utf-8">
<title>Marlow Dermal Studio – Outdoor Banner</title>
<link rel="stylesheet" href="https://fonts.googleapis.com/css2?family=Josefin+Sans:wght@600;700&family=Lato:wght@400;700&display=swap">
<style>
  :root {
    --orange: #f78f20;
    --orange-deep: #ec7f12;
    --white: #ffffff;
    --ink: #2b2b2b;
    --backdrop: #e6e6e6;
    --sky: #5fc5de;
    --sea: #36b3bd;
    --sand: #eef1f1;
  }
  * { margin: 0; padding: 0; box-sizing: border-box; }
  html, body { width: 1200px; height: 818px; overflow: hidden; background: var(--backdrop); }
  .canvas { position: relative; width: 1200px; height: 818px; }
  .banner {
    position: absolute; left: 20px; top: 192px;
    width: 1160px; height: 434px; overflow: hidden;
    font-family: "Josefin Sans", sans-serif; color: var(--white);
  }
  .beach-photo {
    position: absolute; inset: 0;
    background: linear-gradient(180deg, var(--sky) 0%, #8dd6e6 44%, var(--sea) 50%, #7fd0d3 66%, var(--sand) 82%, #f4f2ee 100%);
  }
  .offer-panel { position: absolute; inset: 0; width: 1160px; height: 434px; }
  .brand-name {
    position: absolute; left: 398px; top: 70px; width: 200px;
    text-align: center; color: var(--ink); font-weight: 700; line-height: 1;
  }
  .brand-name .mark {
    display: block; width: 66px; height: 66px; margin: 0 auto 22px;
    border-radius: 50%; background: var(--orange);
  }
  .brand-name .primary { display: block; font-size: 42px; }
  .brand-name .secondary { display: block; font-size: 16px; letter-spacing: 3px; margin-top: 8px; }
  .refresh-tab {
    position: absolute; left: 799px; top: 0; width: 54px; height: 247px;
    background: var(--white); border-radius: 0 0 27px 27px;
  }
  .refresh-tab span {
    position: absolute; left: 50%; top: 128px;
    transform: translate(-50%, -50%) rotate(-90deg);
    color: var(--orange-deep); font-weight: 700; font-size: 36px; letter-spacing: 1px; white-space: nowrap;
  }
  .headline { position: absolute; left: 872px; top: 52px; font-weight: 700; line-height: 1; }
  .headline .line-1 { display: block; font-size: 80px; }
  .headline .line-2 { display: block; font-size: 100px; margin-top: 2px; }
  .service-list {
    position: absolute; left: 618px; top: 266px; width: 498px; height: 39px;
    border: 2px solid var(--white); border-radius: 20px;
    display: flex; align-items: center; justify-content: center; gap: 10px;
    font-weight: 700; font-size: 19px; padding-top: 3px;
  }
  .service-list .divider { width: 2px; height: 22px; background: var(--white); margin-top: -3px; }
  .contact-phone {
    position: absolute; left: 690px; top: 330px; display: flex; align-items: center; gap: 12px;
    font-weight: 700; font-size: 40px; line-height: 1; white-space: nowrap;
  }
  .contact-web {
    position: absolute; left: 704px; top: 382px; display: flex; align-items: center; gap: 14px;
    font-family: "Lato", sans-serif; font-weight: 700; font-size: 17px; white-space: nowrap;
  }
  .contact-rule { position: absolute; left: 1047px; top: 331px; width: 2px; height: 72px; background: var(--white); }
  .social-list { position: absolute; left: 1062px; top: 336px; list-style: none; }
  .social-list li {
    display: flex; align-items: center; gap: 5px; height: 30px; margin-bottom: 8px;
    font-weight: 700; font-size: 14px;
  }
  .social-list li::before { content: ""; width: 11px; height: 11px; border-radius: 50%; background: var(--white); }
</style>
</head>
<body>
<div class="canvas">
  <section class="banner">
    <div class="beach-photo" role="img" aria-label="Photo: smiling woman in a straw sun hat on a bright beach with turquoise sea"></div>

    <svg class="offer-panel" viewBox="0 0 1160 434" aria-hidden="true">
      <path d="M820 0 H1160 V434 H668 C600 400 570 330 580 260 C595 170 680 110 790 100 C810 60 818 30 820 0 Z" fill="var(--orange-deep)"/>
      <path d="M1160 0 V434 H860 C900 360 1000 300 1160 290 Z" fill="var(--orange)" opacity="0.35"/>
    </svg>

    <div class="brand-name">
      <span class="mark"></span>
      <span class="primary">Marlow</span>
      <span class="secondary">Dermal Studio</span>
    </div>

    <div class="refresh-tab"><span>REFRESH</span></div>
    <h1 class="headline"><span class="line-1">YOUR</span><span class="line-2">SKIN</span></h1>

    <p class="service-list">
      <span>LASER HAIR REMOVAL</span><span class="divider"></span>
      <span>VELUXIN</span><span class="divider"></span>
      <span>LIP FILLER</span>
    </p>

    <p class="contact-phone">
      <svg width="36" height="36" viewBox="0 0 24 24" fill="none" stroke="var(--white)" stroke-width="1.6" stroke-linecap="round" stroke-linejoin="round" aria-hidden="true">
        <path d="M22 16.9v3a2 2 0 0 1-2.2 2 19.8 19.8 0 0 1-8.6-3.1 19.5 19.5 0 0 1-6-6A19.8 19.8 0 0 1 2.1 4.2 2 2 0 0 1 4.1 2h3a2 2 0 0 1 2 1.7c.1 1 .4 1.9.7 2.8a2 2 0 0 1-.5 2.1L8 9.9a16 16 0 0 0 6 6l1.3-1.3a2 2 0 0 1 2.1-.4c.9.3 1.8.6 2.8.7a2 2 0 0 1 1.7 2z"/>
        <path d="M15 5a5 5 0 0 1 4 4M15 1a9 9 0 0 1 8 8"/>
      </svg>
      <span>(520) 867-2291</span>
    </p>

    <p class="contact-web">
      <svg width="24" height="24" viewBox="0 0 24 24" fill="none" stroke="var(--white)" stroke-width="1.6" stroke-linecap="round" aria-hidden="true">
        <circle cx="12" cy="12" r="10"/><path d="M2 12h20M12 2a15 15 0 0 1 0 20M12 2a15 15 0 0 0 0 20"/>
      </svg>
      <span>www.MarlowDermalStudio.com</span>
    </p>

    <span class="contact-rule"></span>
    <ul class="social-list">
      <li>Lumora</li>
      <li>Pictavo</li>
    </ul>
  </section>
</div>
</body>
</html>
```